Brightline Energy Product Distribution Brochure

We are looking to have our current brochure for our customers completely redesigned...the idea is to present the relevant information in an attractive way . Our website is brightlineenergyco.example where you can find more information about us. We have included a file with a rough idea of the page order and what each should include but feel free to adapt based on design. The example provided is only for context and doesnt have to be maintained. We will be using the brochure both digitally and in print form. As long as it reads easily and is eye catching, the design can be horizontal or vertical.Final deliverable should be indesign file.

"Our Brands" page: should be limited to one page (space being enough) where it has the header for each one (for example diesel generators) space for one or two lines of text and then the corresponding logos for each of the five categories
Updates

For those asking: the "our brands" page should be a single page layout where there is a header with the corresponding section and space for maybe one line of text followed by the two logos for that category. Each of the product pages should be similar in fashion to the one in the document attached: a photo of the product with some white space and space for the text to be included. We will be posting additional examples today

Target Market(s)

We want to present it to customers both digitally and in print so they can see our products

Industry/Entity Type

Power Generation

Font styles to use
Serif

Requirements
Must have
• Eye catching and able to present the information in a presentable fashion. Rest is up to you.
Nice to have
• Should incorporate the colors of our logo but can also add other depending on design

```html
<!DOCTYPE html>
<html lang="en">
<head>
<meta charset="utf-8">
<title>Brightline Energy – Brochure Inside Pages</title>
<link rel="stylesheet" href="https://fonts.googleapis.com/css2?family=Montserrat:ital,wght@0,400;0,600;1,300&family=Raleway:wght@300;400;800&display=swap">
<style>
  :root {
    --yellow: #fccb05;
    --ink: #1c1c1c;
    --grey-label: #6b6b6b;
    --paper: #ffffff;
    --shade: #e4e4e4;
  }
  * { margin: 0; padding: 0; box-sizing: border-box; }
  html, body { width: 1200px; height: 1200px; overflow: hidden; background: var(--paper); }
  .board { position: relative; width: 1200px; height: 1200px; }
  .spread-label {
    position: absolute; top: 134px;
    font: italic 300 24px "Montserrat", sans-serif; color: var(--grey-label);
  }
  .page {
    position: absolute; top: 216px; width: 548px; height: 776px;
    background: var(--paper); overflow: hidden;
    box-shadow: 0 30px 40px -10px rgba(0,0,0,.18), 0 4px 12px rgba(0,0,0,.06);
  }
  .page-art { position: absolute; inset: 0; width: 548px; height: 776px; }
  .section-bar { position: absolute; left: 0; top: 34px; width: 46px; height: 10px; background: var(--yellow); }
  .section-name {
    position: absolute; left: 56px; top: 33px;
    font: 400 11px "Raleway", sans-serif; color: var(--ink); letter-spacing: .2px;
  }
  .brand {
    position: absolute; right: 50px; top: 37px; display: flex; align-items: center; gap: 5px;
    font: 400 9.5px "Raleway", sans-serif; color: var(--ink); letter-spacing: .3px; text-transform: uppercase;
  }
  .brand-mark { width: 12px; height: 12px; background: var(--yellow); }
  .page-title {
    position: absolute; left: 47px; top: 94px;
    font: 300 32px "Raleway", sans-serif; color: var(--ink); letter-spacing: -.3px; white-space: nowrap;
  }
  .topic {
    position: absolute; left: 47px; top: 156px;
    font: 800 16px "Raleway", sans-serif; color: var(--yellow); letter-spacing: .2px;
  }
  .topic-copy {
    position: absolute; left: 47px; top: 182px; width: 214px;
    font: 400 8.8px/11px "Montserrat", sans-serif; color: var(--ink);
    text-align: justify; hyphens: auto;
  }
  .page-footer {
    position: absolute; left: 47px; top: 741px; display: flex; gap: 43px;
    font: 600 7px "Montserrat", sans-serif; color: var(--ink); text-transform: uppercase;
  }
  .page-left { left: 30px; }
  .page-right { left: 611px; }
</style>
</head>
<body>
<div class="board">
  <p class="spread-label" style="left:30px">Inside</p>
  <p class="spread-label" style="left:613px">Inside</p>

  <!-- Page 5 -->
  <section class="page page-left">
    <svg class="page-art" viewBox="0 0 685 970" aria-hidden="false">
      <defs>
        <linearGradient id="cornerShade" x1="0" y1="0" x2="1" y2="1">
          <stop offset="0" stop-color="#ffffff"/><stop offset="1" stop-color="#d9d9d9"/>
        </linearGradient>
        <linearGradient id="foldShade" x1="0" y1="0" x2="1" y2="0">
          <stop offset="0" stop-color="#e3b600" stop-opacity=".35"/><stop offset="1" stop-color="#fccb05" stop-opacity="0"/>
        </linearGradient>
      </defs>
      <polyline points="685,87 513,257 685,430" fill="none" stroke="var(--yellow)" stroke-width="1.5"/>
      <polyline points="0,392 138,530 0,668" fill="none" stroke="var(--yellow)" stroke-width="1.5"/>
      <polygon points="685,847 563,970 685,970" fill="url(#cornerShade)"/>
      <polygon points="458,317 505,363 213,660 488,933 685,737 685,847 563,970 0,970 0,670 105,670" fill="var(--yellow)"/>
      <polygon points="105,670 400,970 563,970 105,670" fill="url(#foldShade)"/>
      <rect x="263" y="570" width="400" height="160" rx="6" fill="#8a8a80" role="img" aria-label="Photo of an industrial diesel generator set and engine lineup"/>
    </svg>
    <span class="section-bar"></span>
    <p class="section-name">OUR STOCK</p>
    <div class="brand"><span class="brand-mark"></span>Brightline Energy</div>
    <h1 class="page-title">OUR PRODUCTS</h1>
    <h2 class="topic">CONTROLLERS</h2>
    <p class="topic-copy">Fugiant pelluptatis rempe nectibea nati nobitate voluptatur, verum dolorerrum velectur, ut fugit aut aborporepe volluptatem in pro beatios molendi genihillis non nonsequ aersped estius seque volupis es sanis ad que volupta quamus ipic te videndene solum esercid que re audam, nonem es atempos re nim cus et volorument fuga. Da am fugia ipidel maios everum ut venient officit quidi ut quo</p>
    <footer class="page-footer"><span>5</span><span>www.brightlineenergyco.example</span></footer>
  </section>

  <!-- Page 6 -->
  <section class="page page-right">
    <svg class="page-art" viewBox="0 0 685 970">
      <defs>
        <linearGradient id="cornerShade2" x1="0" y1="0" x2="1" y2="1">
          <stop offset="0" stop-color="#ffffff"/><stop offset="1" stop-color="#d9d9d9"/>
        </linearGradient>
        <linearGradient id="foldShade2" x1="0" y1="0" x2="1" y2="0">
          <stop offset="0" stop-color="#e3b600" stop-opacity=".35"/><stop offset="1" stop-color="#fccb05" stop-opacity="0"/>
        </linearGradient>
      </defs>
      <polyline points="685,87 513,257 685,430" fill="none" stroke="var(--yellow)" stroke-width="1.5"/>
      <polyline points="0,392 138,530 0,668" fill="none" stroke="var(--yellow)" stroke-width="1.5"/>
      <polygon points="685,847 563,970 685,970" fill="url(#cornerShade2)"/>
      <polygon points="458,317 505,363 213,660 488,933 685,737 685,847 563,970 0,970 0,670 105,670" fill="var(--yellow)"/>
      <polygon points="105,670 400,970 563,970 105,670" fill="url(#foldShade2)"/>
      <rect x="356" y="525" width="280" height="290" rx="8" fill="#2a2a2a" role="img" aria-label="Photo of an automatic voltage regulator controller board on a clear stand"/>
    </svg>
    <span class="section-bar"></span>
    <p class="section-name">OUR STOCK</p>
    <div class="brand"><span class="brand-mark"></span>Brightline Energy</div>
    <h1 class="page-title">STANDBY GENERATORS</h1>
    <h2 class="topic">CONTROLLERS</h2>
    <p class="topic-copy">Fugiant pelluptatis rempe nectibea nati nobitate voluptatur, verum dolorerrum velectur, ut fugit aut aborporepe volluptatem in pro beatios molendi genihillis non nonsequ aersped estius seque volupis es sanis ad que volupta quamus ipic te videndene solum esercid que re audam, nonem es atempos re nim cus et volorument fuga. Da am fugia ipidel maios everum ut venient officit quidi ut quo</p>
    <footer class="page-footer"><span>6</span><span>www.brightlineenergyco.example</span></footer>
  </section>
</div>
</body>
</html>
```